Home Staging Company needs business card design

We're a home staging company called Brightly Settled Home Staging. We would like a business card design that includes aqua and gray. Our current logo of house within chair is fine but I find we almost always use the logo in one color. I'll upload images of front and back of our current card and our logo. Note that we have dropped "Solutions" from our company name and don't want to include it on the card.

Target Market(s)

Realtors and homeowners - people interested in selling their homes

Contact Information for Business Card

Marisol Thistlewood
Brightly Settled Home Staging
757-555-0193
www.brightlysettled.com
marisol@brightlysettled.com

Font styles to use
Serif
Script

Requirements
Must have
• My logo and contact details
• UPDATE***
• I forgot to say that the company name should be included on the front of the card somehow.

```html
<!DOCTYPE html>
<html lang="en">
<head>
<meta charset="utf-8">
<title>Brightly Settled Home Staging — Business Card</title>
<link href="https://fonts.googleapis.com/css2?family=Didact+Gothic&display=swap" rel="stylesheet">
<style>
  :root {
    --backdrop: #3b3b3b;
    --card: #1d1d1e;
    --card-edge: #141415;
    --gloss: #4a4a4c;
    --faint: #2b2b2c;
    --aqua: #4fb8c3;
    --white: #f2f2f2;
    --gray: #a9a9a9;
  }
  * { box-sizing: border-box; margin: 0; padding: 0; }
  html, body { width: 799px; height: 1200px; overflow: hidden; }
  body {
    background: var(--backdrop);
    font-family: "Didact Gothic", "Century Gothic", sans-serif;
    position: relative;
  }
  .card {
    position: absolute;
    left: 90px;
    width: 620px;
    height: 354px;
    background: var(--card);
    border: 1px solid var(--card-edge);
    box-shadow: 0 14px 30px rgba(0,0,0,.45);
    overflow: hidden;
  }
  .card--front { top: 120px; }
  .card--back { top: 720px; }

  .front-mark {
    position: absolute;
    inset: 0;
    display: flex;
    align-items: center;
    justify-content: center;
    gap: 18px;
  }
  .front-mark__dot {
    width: 34px; height: 34px;
    border-radius: 50%;
    background: var(--gloss);
  }
  .front-mark__name {
    color: var(--gloss);
    font-size: 30px;
    letter-spacing: .5px;
  }

  .back-decor {
    position: absolute;
    right: -60px;
    bottom: -70px;
    width: 330px;
    height: 330px;
    border-radius: 50%;
    background: var(--faint);
  }
  .contact {
    position: absolute;
    left: 56px;
    top: 44px;
    color: var(--white);
  }
  .contact__name { font-size: 24px; letter-spacing: .3px; }
  .contact__name .surname { color: var(--aqua); }
  .contact__title { font-size: 12px; color: var(--gray); margin-top: 2px; margin-bottom: 22px; }
  .contact__list { list-style: none; font-size: 15px; line-height: 24px; }
  .contact__list li { display: flex; align-items: center; gap: 10px; }
  .contact__list svg { width: 13px; height: 13px; flex: none; }
  .contact__list .accent { color: var(--aqua); }

  .brand {
    position: absolute;
    left: 56px;
    bottom: 52px;
    display: flex;
    align-items: center;
    gap: 12px;
  }
  .brand__dot {
    width: 26px; height: 26px;
    border-radius: 50%;
    background: var(--aqua);
  }
  .brand__name { color: var(--white); font-size: 24px; }
</style>
</head>
<body>
  <section class="card card--front" aria-label="Card front">
    <div class="front-mark">
      <span class="front-mark__dot"></span>
      <span class="front-mark__name">Brightly Settled Home Staging</span>
    </div>
  </section>

  <section class="card card--back" aria-label="Card back">
    <div class="back-decor"></div>
    <div class="contact">
      <p class="contact__name">Marisol <span class="surname">Thistlewood</span></p>
      <p class="contact__title">Managing Director</p>
      <ul class="contact__list">
        <li>
          <svg viewBox="0 0 16 16" fill="var(--aqua)"><path d="M3.6 1.5l2.2 2.6-1.3 1.6c.9 2 2.4 3.5 4.4 4.4l1.6-1.3 2.6 2.2-1.3 2.2C7 13 3 9 1.6 3z"/></svg>
          757-555-0193
        </li>
        <li>
          <svg viewBox="0 0 16 16" fill="none" stroke="var(--aqua)" stroke-width="1.4"><circle cx="8" cy="8" r="6.5"/><ellipse cx="8" cy="8" rx="2.8" ry="6.5"/><path d="M1.5 8h13"/></svg>
          <span>www.<span class="accent">brightlysettled</span>.com</span>
        </li>
        <li>
          <svg viewBox="0 0 16 16" fill="var(--aqua)"><rect x="1" y="3.5" width="14" height="9" rx="1"/><path d="M1.5 4l6.5 5 6.5-5" stroke="var(--card)" stroke-width="1.3" fill="none"/></svg>
          marisol@brightlysettled.com
        </li>
      </ul>
    </div>
    <div class="brand">
      <span class="brand__dot"></span>
      <span class="brand__name">Brightly Settled Home Staging</span>
    </div>
  </section>
</body>
</html>
```